Corvane Paintless Dent Removal

Our company works on vehicles removing dents using a highly skilled trade which the metal is massaged out with special tools without disturbing the original paint, hence paintless dent removal. Besides keeping the paint and metal original its also very environmentally friendly since no paint or toxic fillers are used. Also we we are one of the most experienced companies in the business with 25 years

Target Market(s)

Retail Automobile consumers, Auto Dealerships and Auto Body Shops

Industry/Entity Type

Auto Repair

Contact Information for Business Card

Dale Hollister
PO Box 518 Brookmere, NY 11962
631-555-0148
corvanepdr@mailbox-example.com
website corvanepdr.example
youtube corvane paintless dent removal
25 years of experience removing Dents, Dings and Hail Damage

Font styles to use
Serif
Sans Serif

Colors

Designer to choose colors to be used in the design.

Requirements
Must have
• I do like things that are simple but classy and somewhat bold, also I like my logo so that should be somewhat important

```html
<!DOCTYPE html>
<html lang="en">
<head>
<meta charset="utf-8">
<title>Corvane Paintless Dent Removal – Business Card</title>
<link rel="stylesheet" href="https://fonts.googleapis.com/css2?family=Roboto:wght@400;700;900&family=Roboto+Condensed:wght@700&display=swap">
<style>
  :root {
    --backdrop: #e6e4e0;
    --card-white: #f4f4f4;
    --navy: #1b2f5c;
    --lime: #7dc40f;
    --text-grey: #555555;
    --rule-grey: #8c8c8c;
    --badge-dark: #1a1a1a;
    --badge-gold: #d9a431;
    --white: #ffffff;
  }
  * { margin: 0; padding: 0; box-sizing: border-box; }
  html, body {
    width: 1200px; height: 960px; overflow: hidden;
    background: var(--backdrop);
    font-family: "Roboto", Arial, sans-serif;
  }
  .canvas { position: relative; width: 1200px; height: 960px; }

  .card { position: absolute; width: 600px; height: 342px; box-shadow: 0 4px 10px rgba(0,0,0,0.35); overflow: hidden; }

  /* Front */
  .card-front { left: 314px; top: 113px; background: var(--card-white); }
  .front-stripe-lime { position: absolute; left: 0; right: 0; top: 325px; height: 3px; background: var(--lime); }
  .front-stripe-navy { position: absolute; left: 0; right: 0; top: 330px; height: 12px; background: var(--navy); }

  .experience-badge {
    position: absolute; left: 36px; top: 34px; width: 72px; height: 72px; border-radius: 50%;
    background: var(--badge-dark); border: 4px solid var(--badge-gold);
  }

  .brand-mark {
    position: absolute; right: 38px; top: 50px; text-align: center; color: var(--navy);
    font-weight: 900; line-height: 1;
  }
  .brand-mark .brand-name { font-size: 34px; letter-spacing: 0.5px; text-transform: uppercase; }
  .brand-mark .brand-tagline { font-size: 13px; margin-top: 3px; }

  .holder-name {
    position: absolute; left: 38px; top: 208px;
    font-family: "Roboto Condensed", Arial, sans-serif; font-weight: 700;
    font-size: 21px; color: var(--navy); letter-spacing: 0.3px;
  }
  .name-rule { position: absolute; left: 38px; width: 523px; top: 241px; height: 1px; background: var(--rule-grey); }

  .contact-list { position: absolute; left: 38px; top: 254px; list-style: none; font-size: 14px; color: var(--text-grey); }
  .contact-list li { display: flex; align-items: center; height: 19px; }
  .contact-list svg { width: 13px; height: 13px; margin-right: 9px; fill: var(--navy); flex: none; }

  .postal-block { position: absolute; right: 36px; top: 256px; text-align: right; font-size: 14px; line-height: 19px; color: var(--text-grey); }

  /* Back */
  .card-back { left: 311px; top: 472px; background: var(--lime); height: 343px; }
  .card-back .brand-mark { right: auto; left: 0; width: 600px; top: 140px; }
  .card-back .brand-mark .brand-name { font-size: 40px; }
  .card-back .brand-mark .brand-tagline { font-size: 15px; }
  .back-web {
    position: absolute; left: 0; width: 600px; top: 280px; text-align: center;
    color: var(--white); font-size: 14px; letter-spacing: 5px;
  }
</style>
</head>
<body>
<main class="canvas">
  <section class="card card-front">
    <div class="experience-badge" role="img" aria-label="25 years of experience badge"></div>

    <div class="brand-mark">
      <div class="brand-name">Corvane</div>
      <div class="brand-tagline">Paintless Dent Removal</div>
    </div>

    <h1 class="holder-name">DALE HOLLISTER</h1>
    <div class="name-rule"></div>

    <ul class="contact-list">
      <li>
        <svg viewBox="0 0 24 24" aria-hidden="true"><path d="M6.6 10.8a15.1 15.1 0 0 0 6.6 6.6l2.2-2.2c.3-.3.7-.4 1-.2 1.1.4 2.3.6 3.6.6.6 0 1 .4 1 1V20c0 .6-.4 1-1 1A17 17 0 0 1 3 4c0-.6.4-1 1-1h3.5c.6 0 1 .4 1 1 0 1.3.2 2.5.6 3.6.1.3 0 .7-.2 1z"/></svg>
        631-555-0148
      </li>
      <li>
        <svg viewBox="0 0 24 24" aria-hidden="true"><path d="M2 5h20v14H2z M3 6l9 7 9-7" stroke="#f4f4f4" stroke-width="1.5"/></svg>
        corvanepdr@mailbox-example.com
      </li>
      <li>
        <svg viewBox="0 0 24 24" aria-hidden="true"><rect x="2" y="5" width="20" height="14" rx="2"/></svg>
        corvane paintless dent removal
      </li>
    </ul>

    <address class="postal-block" style="font-style:normal">
      PO Box 518<br>
      Brookmere, NY 11962<br>
      www.corvanepdr.example
    </address>

    <div class="front-stripe-lime"></div>
    <div class="front-stripe-navy"></div>
  </section>

  <section class="card card-back">
    <div class="brand-mark">
      <div class="brand-name">Corvane</div>
      <div class="brand-tagline">Paintless Dent Removal</div>
    </div>
    <p class="back-web">www.corvanepdr.example</p>
  </section>
</main>
</body>
</html>
```